Brenwick Coaching Website

I would like someone to design my website. I have an existing site which is really basic and needs an overhaul. I have attached a powerpoint with all the information I require. I am flexible with the design and layout and am ok with graphics being added to enhance the attractiveness of the site.

```html
<!DOCTYPE html>
<html lang="en">
<head>
<meta charset="utf-8">
<title>Brenwick Coaching</title>
<link rel="stylesheet" href="https://fonts.googleapis.com/css2?family=Outfit:wght@400;500&family=Roboto:wght@400&display=swap">
<style>
  :root {
    --orange: #f26a35;
    --orange-light: #fe8a5e;
    --orange-dark: #f05a28;
    --blue: #1f6fbf;
    --ink: #1c1c1c;
    --body-text: #3b3b3b;
    --panel: #f7f7f7;
    --panel-line: #dedede;
    --footer: #000000;
    --white: #ffffff;
    --social: #5a5a5a;
  }
  * { box-sizing: border-box; margin: 0; padding: 0; }
  html, body { width: 1200px; height: 643px; overflow: hidden; background: var(--white); }
  .site {
    position: relative; width: 1200px; height: 643px;
    font-family: "Outfit", sans-serif; color: var(--ink);
    border-top: 5px solid var(--orange);
  }
  .brand {
    position: absolute; left: 53px; top: 42px;
    font-family: "Outfit", sans-serif; font-weight: 500;
    font-size: 34px; line-height: 1; color: var(--blue);
    display: flex; align-items: center; gap: 12px;
  }
  .brand-mark { width: 14px; height: 14px; background: var(--orange); }
  .contact { position: absolute; left: 866px; top: 42px; font-size: 16px; }
  .contact-row { display: flex; align-items: center; height: 36px; }
  .contact-row svg { width: 24px; height: 18px; margin-right: 10px; flex: none; }
  .nav { position: absolute; left: 56px; top: 136px; width: 250px; list-style: none; }
  .nav-item {
    height: 89px; margin-bottom: 12.5px;
    background: linear-gradient(to bottom, var(--orange-light), var(--orange-dark));
    color: var(--white); font-size: 16.5px;
    display: flex; align-items: center; padding-left: 28px;
  }
  .main-panel {
    position: absolute; left: 338px; top: 135px; width: 792px; height: 396px;
    background: var(--panel); border: 1px solid var(--panel-line);
  }
  .main-title {
    position: absolute; left: 30px; top: 24px;
    font-size: 28px; font-weight: 400; color: var(--blue);
  }
  .intro {
    position: absolute; left: 30px; top: 85px; width: 440px;
    font-family: "Roboto", sans-serif; font-size: 12.6px; line-height: 27px;
    color: var(--body-text); text-align: justify;
  }
  .profile-card {
    position: absolute; left: 520px; top: 22px; width: 249px; height: 293px;
    background: var(--panel); border: 1px solid var(--panel-line); padding: 5px;
  }
  .profile-photo {
    height: 231px;
    background: linear-gradient(160deg, #b9a893 0%, #8a7a66 45%, #4a3a30 100%);
  }
  .profile-link { font-size: 20px; padding: 13px 0 0 15px; color: #333; }
  .offer-strip {
    position: absolute; left: -1px; bottom: -1px; width: 792px; height: 55px;
    border: 1px solid var(--panel-line); background: var(--panel);
    font-family: "Roboto", sans-serif; font-size: 12.8px; color: #333;
    display: flex; align-items: center; padding-left: 31px;
  }
  .footer {
    position: absolute; left: 0; bottom: 0; width: 1200px; height: 77px;
    background: var(--footer); color: var(--white);
  }
  .copyright { position: absolute; left: 58px; top: 31px; font-size: 14px; }
  .social { position: absolute; left: 976px; top: 25px; display: flex; gap: 17px; list-style: none; }
  .social-square { width: 25px; height: 25px; background: var(--social); }
</style>
</head>
<body>
<div class="site">
  <header>
    <div class="brand"><span class="brand-mark"></span>Brenwick Coaching</div>
    <div class="contact">
      <div class="contact-row">
        <svg viewBox="0 0 24 18" aria-hidden="true"><path d="M2 7c0-3 5-5 10-5s10 2 10 5l-4 1-1-3H7L6 8z" fill="#f26a35"/><rect x="6" y="9" width="12" height="8" rx="2" fill="#f26a35"/><circle cx="12" cy="13" r="2" fill="#fff"/></svg>
        <span>1300 555 017</span>
      </div>
      <div class="contact-row">
        <svg viewBox="0 0 24 18" aria-hidden="true"><rect x="1" y="2" width="22" height="15" fill="#f26a35"/><path d="M1 2l11 8 11-8" fill="none" stroke="#fff" stroke-width="1.6"/></svg>
        <span>Maren.Holt@brenwickcoaching.com</span>
      </div>
    </div>
  </header>

  <ul class="nav">
    <li class="nav-item">Individual Coaching (1)</li>
    <li class="nav-item">Group Work (2)</li>
    <li class="nav-item">Resources (3)</li>
    <li class="nav-item">Inspiration Booth (5)</li>
  </ul>

  <main class="main-panel">
    <h1 class="main-title">Brenwick Coaching</h1>
    <p class="intro">Welcome to Brenwick Coaching where we put a new perspective on the way you work, live and play. Through our programs you will learn new skills &amp; techniques to enable you to break through the barriers that have kept you from reaching your full potential up to now. Welcome to Brenwick Coaching where we put a new perspective on the way you work, live and play. Through our programs you will learn new skills &amp; techniques to enable you to break through the barriers that have kept you from reaching your full potential up to now.</p>
    <div class="profile-card">
      <div class="profile-photo" role="img" aria-label="Portrait photograph of coach Maren outdoors among trees"></div>
      <div class="profile-link">About &nbsp;Maren (6)</div>
    </div>
    <div class="offer-strip">Get your free 30 minute introductory coaching session... (4)</div>
  </main>

  <footer class="footer">
    <p class="copyright">©2014 Brenwick Coaching, All Rights Reserved.</p>
    <ul class="social">
      <li class="social-square"></li>
      <li class="social-square"></li>
      <li class="social-square"></li>
      <li class="social-square"></li>
    </ul>
  </footer>
</div>
</body>
</html>
```